I am a home builder and developer

I would like some sort of architectural design like a pencil type of drawing of a house but want it to be professional looking and two sided.

Simply I am a custom home builder and land developer. I would like a new design other than what I have now that's what I thought y'all did. I like mostly black maybe with an pencil type of drawing of a house. Like an architectural look.

Industry/Entity Type

Home Builder

```html
<!DOCTYPE html>
<html lang="en">
<head>
<meta charset="utf-8">
<title>R&amp;L Building Inc – Business Card</title>
<link rel="stylesheet" href="https://fonts.googleapis.com/css2?family=Open+Sans:wght@400;700;800&display=swap">
<style>
  :root {
    --brand-blue: #1c3f95;
    --brand-grey: #6b6b6b;
    --card-white: #ffffff;
    --ink: #2a2a2a;
    --stage: #e9e9e9;
    --sketch-light: #f4f5f6;
    --sketch-mid: #d6d9dd;
  }
  * { box-sizing: border-box; margin: 0; padding: 0; }
  html, body {
    width: 1200px; height: 900px; overflow: hidden;
    background: var(--stage);
    font-family: "Open Sans", Arial, sans-serif;
  }
  .canvas { position: relative; width: 1200px; height: 900px; }
  .card {
    position: absolute; left: 250px; width: 700px; height: 400px;
    background: var(--card-white); overflow: hidden;
    box-shadow: 0 6px 18px rgba(0,0,0,0.15);
  }
  .card--back { top: 30px; }
  .card--front { top: 470px; }

  /* Back side */
  .architectural-visual {
    position: absolute; left: 30px; top: 0; width: 540px; height: 330px;
    background: radial-gradient(ellipse at 45% 35%, var(--card-white) 0%, var(--sketch-light) 45%, var(--sketch-mid) 100%);
    opacity: 0.9;
  }
  .wordmark {
    position: absolute; right: 40px; color: var(--brand-blue);
    font-weight: 800; text-align: center; line-height: 1;
  }
  .card--back .wordmark { bottom: 30px; }
  .card--back .wordmark__initials { font-size: 72px; letter-spacing: 2px; }
  .card--back .wordmark__suffix { font-size: 30px; letter-spacing: 1px; margin-top: 4px; }

  /* Front side */
  .decor { position: absolute; inset: 0; width: 700px; height: 400px; }
  .holder-name {
    position: absolute; left: 72px; top: 26px;
    color: var(--brand-blue); font-weight: 700; font-size: 20px;
  }
  .contact-list {
    position: absolute; left: 34px; top: 236px; list-style: none;
    color: var(--ink); font-size: 16px;
  }
  .contact-list li { display: flex; align-items: center; gap: 10px; height: 24px; }
  .contact-list svg { width: 14px; height: 14px; fill: var(--brand-blue); }
  .card--front .wordmark { top: 150px; right: 50px; }
  .card--front .wordmark__initials { font-size: 110px; letter-spacing: 3px; }
  .card--front .wordmark__suffix { font-size: 44px; letter-spacing: 1px; margin-top: 4px; }
</style>
</head>
<body>
<main class="canvas">

  <section class="card card--back" aria-label="Business card, back">
    <div class="architectural-visual" role="img" aria-label="Architectural illustration of a 3D house floor plan model over pencil blueprint drawings"></div>
    <div class="wordmark">
      <div class="wordmark__initials">R&amp;L</div>
      <div class="wordmark__suffix">BUILDING INC</div>
    </div>
  </section>

  <section class="card card--front" aria-label="Business card, front">
    <svg class="decor" viewBox="0 0 700 400" aria-hidden="true">
      <polygon points="0,20 48,20 34,48 0,48" fill="var(--brand-blue)"/>
      <polygon points="50,20 62,20 62,48 36,48" fill="var(--brand-grey)"/>
      <polygon points="0,318 300,318 284,340 0,340" fill="var(--brand-blue)"/>
      <polygon points="306,340 700,340 700,400 262,400" fill="var(--brand-grey)"/>
    </svg>

    <h1 class="holder-name">Daniel Brooks</h1>

    <ul class="contact-list">
      <li>
        <svg viewBox="0 0 24 24"><path d="M6.6 10.8a15.2 15.2 0 0 0 6.6 6.6l2.2-2.2a1 1 0 0 1 1-.25 11.4 11.4 0 0 0 3.6.57 1 1 0 0 1 1 1V20a1 1 0 0 1-1 1A17 17 0 0 1 3 4a1 1 0 0 1 1-1h3.5a1 1 0 0 1 1 1c0 1.25.2 2.45.57 3.57a1 1 0 0 1-.25 1z"/></svg>
        <span>555-204-3187</span>
      </li>
      <li>
        <svg viewBox="0 0 24 24"><path d="M2 5h20v14H2z M2 5l10 8 10-8" /></svg>
        <span>rlbuildinc@example.com</span>
      </li>
    </ul>

    <div class="wordmark">
      <div class="wordmark__initials">R&amp;L</div>
      <div class="wordmark__suffix">BUILDING INC</div>
    </div>
  </section>

</main>
</body>
</html>
```